Business Card Design

I already have a company logo for my company. I have a logo for the manufacturer we represent. I want a professional business card design.

```html
<!DOCTYPE html>
<html lang="en">
<head>
<meta charset="utf-8">
<title>Signal Guard LLC — Business Card</title>
<link rel="stylesheet" href="https://fonts.googleapis.com/css2?family=Montserrat:wght@400;500;700;800&display=swap">
<style>
  :root {
    --backdrop: #2b2b2d;
    --card: #1b1b1c;
    --card-edge: #111112;
    --ink-light: #e9e9ea;
    --ink-muted: #c9c9cb;
    --accent-red: #e2262b;
  }
  * { box-sizing: border-box; margin: 0; padding: 0; }
  html, body {
    width: 1200px; height: 688px; overflow: hidden;
    background: var(--backdrop);
    font-family: "Montserrat", sans-serif;
  }
  .stage {
    position: relative; width: 1200px; height: 688px;
    display: flex; align-items: center; justify-content: center; gap: 40px;
  }
  .card {
    position: relative; width: 540px; height: 309px;
    background: var(--card);
    border: 1px solid var(--card-edge);
    box-shadow: 0 18px 40px rgba(0,0,0,0.45);
    overflow: hidden;
  }
  .wordmark {
    display: flex; align-items: center; gap: 12px;
    color: var(--ink-light);
    font-weight: 800; text-transform: uppercase; letter-spacing: 0.04em;
    line-height: 1;
  }
  .wordmark__square { width: 22px; height: 22px; background: var(--accent-red); flex: none; }

  /* Front */
  .card--front { display: flex; align-items: center; justify-content: center; }
  .card--front .wordmark { font-size: 38px; }
  .card--front .wordmark__square { width: 30px; height: 30px; }

  /* Back */
  .card--back .wordmark { position: absolute; left: 30px; top: 34px; font-size: 24px; z-index: 2; }
  .card--back .wordmark__square { width: 18px; height: 18px; }
  .card__stripes {
    position: absolute; right: 0; top: 120px; width: 300px; height: 120px;
  }
  .contact { position: absolute; left: 30px; top: 104px; color: var(--ink-light); z-index: 2; }
  .contact__name { color: var(--accent-red); font-weight: 700; font-size: 20px; line-height: 1.1; }
  .contact__title { font-size: 12px; font-weight: 500; color: var(--ink-muted); margin-top: 3px; }
  .contact__address { font-size: 12px; line-height: 1.4; margin-top: 12px; color: var(--ink-muted); }
  .contact__list { list-style: none; margin-top: 10px; font-size: 12px; color: var(--ink-light); }
  .contact__list li { display: flex; align-items: center; gap: 10px; line-height: 1.7; }
  .contact__icon { width: 11px; height: 11px; flex: none; }
</style>
</head>
<body>
  <main class="stage">
    <section class="card card--front" aria-label="Card front">
      <div class="wordmark"><span class="wordmark__square"></span>Signal Guard LLC</div>
    </section>

    <section class="card card--back" aria-label="Card back">
      <div class="wordmark"><span class="wordmark__square"></span>Signal Guard LLC</div>

      <svg class="card__stripes" viewBox="0 0 300 120" aria-hidden="true">
        <polygon points="150,20 300,20 300,38 130,38" fill="var(--accent-red)"/>
        <polygon points="100,50 300,50 300,68 80,68" fill="var(--accent-red)"/>
        <polygon points="50,80 250,80 230,98 30,98" fill="var(--accent-red)"/>
      </svg>

      <div class="contact">
        <p class="contact__name">Dana Keller</p>
        <p class="contact__title">Managing Director</p>
        <p class="contact__address">2840 Alder Ave<br>Denver, CO 80205</p>
        <ul class="contact__list">
          <li>
            <svg class="contact__icon" viewBox="0 0 12 12" aria-hidden="true"><path fill="var(--accent-red)" d="M2.5 1 4.5 1 5.3 3.6 4 4.6C4.6 6 6 7.4 7.4 8L8.4 6.7 11 7.5 11 9.5C11 10.3 10.3 11 9.5 11 5 11 1 7 1 2.5 1 1.7 1.7 1 2.5 1Z"/></svg>
            555.214.0187
          </li>
          <li>
            <svg class="contact__icon" viewBox="0 0 12 12" aria-hidden="true"><rect x="0.5" y="2" width="11" height="8" fill="var(--accent-red)"/><path d="M1 2.5 6 6.5 11 2.5" fill="none" stroke="var(--card)" stroke-width="1.1"/></svg>
            info@signalguardllc.com
          </li>
          <li>
            <svg class="contact__icon" viewBox="0 0 12 12" aria-hidden="true"><circle cx="6" cy="6" r="5" fill="none" stroke="var(--accent-red)" stroke-width="1.4"/><path d="M1 6H11M6 1C3.8 3.5 3.8 8.5 6 11M6 1C8.2 3.5 8.2 8.5 6 11" fill="none" stroke="var(--accent-red)" stroke-width="1"/></svg>
            www.signalguardllc.com
          </li>
        </ul>
      </div>
    </section>
  </main>
</body>
</html>
```